Redesign Merle's RV Park & Lodge Website, Leeds, North Dakota

I need a totally re-designed website for my RV Park / Lodge. I want to not only provide information on my RV Park / Lodge, I want to provide my customers with information on the town and area attractions. I want to provide rate information. Ideally, I would like to have a button/page for each section: Welcome & Information, Area Attractions, Welcome to Leeds, Rates, Who's Merle?!, FAQ's and Where are we?. I don't know if this would be more expensive the more pages you have? If more pages is too expensive, then we can combine info on less pages. I want my logo included on the web page. I want Studio Flock to take down my old website and use the same address to put up my newly designed website.

Target Market(s)

Full time RVers, People who camp, hunt fish, People who recreate on Devils Lake, People who are looking for meeting/conference space, people who are looking for party venue

Industry/Entity Type

Accommodation

Number of Pages Required

3 page

Requirements
Must have
• I want a cozy, welcoming type web site. No super dark colors. Bright and cheerful.
• Must be simple and organized.
• NOTE: I have a file of pictures of the interior of Merle's Lodge that must be included in website. Please request this file if you will be designing my project as the files are too large to upload through Studio Flock.
Nice to have
• If you cannot open any of the files listed, please notify me.
Should not have
• No stark or super-formal designs.

```html
<!DOCTYPE html>
<html lang="en">
<head>
<meta charset="utf-8">
<title>Merle's RV Park &amp; Lodge — Leeds, North Dakota</title>
<link href="https://fonts.googleapis.com/css2?family=Roboto:wght@400;500;700&family=Open+Sans:wght@400;600&display=swap" rel="stylesheet">
<style>
:root{
  --maroon:#7a1f24;
  --maroon-dark:#5e1418;
  --green:#4b6a2e;
  --green-dark:#3c5624;
  --ink:#1d1d1d;
  --text:#333;
  --grey-bg:#ececec;
  --nav:#1f1f1f;
  --footer:#161616;
  --white:#fff;
  --tick:#6b7b2b;
}
*{box-sizing:border-box;margin:0;padding:0}
html,body{width:1200px;height:4091px;overflow:hidden}
body{font-family:"Open Sans",Arial,sans-serif;color:var(--text);background:var(--white);font-size:15px;line-height:1.7}
h1,h2,h3,h4{font-family:"Roboto",Arial,sans-serif;font-weight:700;color:var(--ink)}
section,header,nav,footer{position:relative;width:1200px}

/* header */
.site-header{height:142px;display:flex;align-items:center;padding:0 100px}
.brand{display:flex;align-items:center;gap:14px}
.brand-mark{width:40px;height:40px;background:var(--maroon)}
.brand-name{font-family:"Roboto",sans-serif;font-weight:700;font-size:19px;line-height:1.2;color:var(--ink)}
.header-call{margin-left:auto;display:flex;align-items:center;gap:12px;font-family:"Roboto",sans-serif;font-size:17px;line-height:1.3;color:var(--ink)}
.search{margin-left:40px;width:240px;height:42px;border:1px solid #ccc;border-radius:3px;display:flex;align-items:center;justify-content:space-between;padding:0 12px;font-size:14px;color:#777}

/* nav */
.main-nav{height:54px;background:var(--nav);display:flex;padding-left:100px}
.main-nav a{color:var(--white);text-decoration:none;font-family:"Roboto",sans-serif;font-weight:500;font-size:14px;text-transform:uppercase;display:flex;align-items:center;padding:0 20px}
.main-nav a.active{background:var(--maroon)}

/* hero */
.hero{height:554px;overflow:hidden}
.hero-photo{position:absolute;inset:0;background:linear-gradient(180deg,#8fa9c4 0%,#6f8f4c 45%,#3f6a24 100%)}
.hero-text{position:absolute;left:775px;top:110px;width:340px;color:var(--white)}
.hero-text h1{color:var(--white);font-size:50px;line-height:1.1;margin-bottom:16px}
.hero-text p{font-size:15px;line-height:1.5;margin-bottom:16px}
.btn{display:inline-block;font-family:"Roboto",sans-serif;font-weight:700;font-size:14px;text-transform:uppercase;text-decoration:none;padding:8px 20px;border-radius:20px}
.btn-maroon{background:var(--maroon);color:var(--white)}
.btn-outline{border:2px solid var(--maroon);color:var(--maroon);border-radius:4px;padding:8px 22px}
.btn-outline-light{border:2px solid var(--white);color:var(--white);border-radius:4px;padding:8px 22px}
.arrow{position:absolute;top:260px}
.hero-curve{position:absolute;left:0;bottom:0}

/* welcome */
.welcome{height:314px;text-align:center;padding-top:0}
.welcome-mark{width:70px;height:70px;background:var(--maroon);margin:0 auto 30px}
.welcome h2{font-size:31px;line-height:1.25;margin-bottom:22px;text-transform:uppercase}
.welcome p{width:1000px;margin:0 auto;font-size:15px}

/* lodge green */
.lodge-intro{height:660px;background:var(--green);color:var(--white);padding-top:50px}
.lodge-intro h2{color:var(--white);text-align:center;font-size:36px;margin-bottom:24px}
.lodge-intro .lead{width:1000px;margin:0 auto;text-align:center;font-size:14.5px}
.meeting{position:absolute;left:100px;top:370px;width:460px}
.meeting h3{color:var(--white);font-size:31px;line-height:1.25;margin-bottom:18px;text-transform:uppercase}
.meeting p{font-size:14px}
.meeting-photo{position:absolute;left:630px;top:300px;width:470px;height:280px;border:4px solid var(--white);background:linear-gradient(160deg,#8a3b2e,#c9b9a2 60%,#6f4d3a)}

/* feature rows */
.feature{display:flex}
.feature-lodge{height:471px;background:var(--grey-bg)}
.round-photo{position:absolute;width:340px;height:340px;border-radius:50%;border:6px solid var(--white);box-shadow:0 0 0 2px #bbb}
.feature-list h3{font-size:34px;margin-bottom:10px;text-transform:uppercase}
.feature-list .sub{font-size:14px;color:var(--green);margin-bottom:6px}
.feature-list ul{list-style:none}
.feature-list li{position:relative;padding-left:26px;font-size:13.5px;line-height:2.05}
.feature-list li::before{content:"";position:absolute;left:0;top:9px;width:12px;height:12px;border-radius:50%;background:var(--tick)}

/* rv park */
.rv-park{height:800px;text-align:center;padding-top:60px}
.rv-park h2{font-size:36px;margin-bottom:20px}
.rv-park p{width:1000px;margin:0 auto 16px;font-size:15px}
.rv-park .feature-list{text-align:left}

/* tents */
.tents{height:436px;background:var(--maroon-dark);background:linear-gradient(180deg,#6e1a1f,#5a1418);color:var(--white);text-align:center;padding-top:110px}
.tents h2{color:var(--white);font-size:36px;margin-bottom:18px}
.tents p{width:1040px;margin:0 auto 24px;font-size:15px}

/* testimonials */
.testimonials{height:283px;text-align:center;padding-top:80px}
.testimonials h2{font-size:32px;line-height:1.3;margin-bottom:22px;text-transform:uppercase}

/* footer */
.site-footer{height:377px;background:var(--footer);color:#ddd}
.footer-brand{position:absolute;left:100px;top:55px;display:flex;flex-direction:column;align-items:center;gap:14px;width:130px}
.footer-brand .brand-mark{width:70px;height:70px;background:var(--white)}
.footer-brand .brand-name{color:var(--white);text-align:center;font-size:19px}
.footer-col{position:absolute;top:40px}
.footer-col h4{color:var(--white);font-size:19px;margin-bottom:18px;text-transform:uppercase}
.footer-col p,.footer-col li{font-size:13px;line-height:1.6}
.contact-row{display:flex;gap:14px;margin-bottom:14px}
.socials{display:flex;gap:8px;margin-top:6px}
.socials span{width:24px;height:24px;border-radius:50%;border:1.5px solid #ccc}
.field{width:285px;height:42px;background:var(--white);margin:16px 0 14px;padding:0 12px;display:flex;align-items:center;color:#777;font-size:12px}
.btn-subscribe{background:var(--green);color:var(--white);font-size:13px;padding:8px 14px;border-radius:2px}
.quick-links{list-style:none}
.quick-links li{position:relative;padding-left:14px}
.quick-links li::before{content:"";position:absolute;left:0;top:7px;border:4px solid transparent;border-left:5px solid #ddd}
.copyright{position:absolute;left:0;bottom:0;width:1200px;height:61px;border-top:1px solid #2e2e2e;display:flex;align-items:center;justify-content:center;font-size:13px;color:#ccc}
</style>
</head>
<body>

<header class="site-header">
  <div class="brand">
    <span class="brand-mark"></span>
    <span class="brand-name">Merle's RV Park<br>&amp; Lodge<br>Leeds ND</span>
  </div>
  <div class="header-call">
    <svg width="36" height="36" viewBox="0 0 36 36"><circle cx="18" cy="18" r="16" fill="none" stroke="#7a1f24" stroke-width="2"/><path d="M12 10l4 0 1 5-2 2c1 2 3 4 5 5l2-2 5 1v4c-9 1-16-6-15-15z" fill="#7a1f24"/></svg>
    <span>Call Us :<br>701-555-0142</span>
  </div>
  <div class="search"><span>search</span>
    <svg width="14" height="14" viewBox="0 0 14 14"><circle cx="6" cy="6" r="4.5" fill="none" stroke="#333" stroke-width="1.6"/><path d="M9.5 9.5l3.5 3.5" stroke="#333" stroke-width="1.6"/></svg>
  </div>
</header>

<nav class="main-nav">
  <a class="active" href="#">Home</a>
  <a href="#">Welcome &amp; Information</a>
  <a href="#">Area Attractions</a>
  <a href="#">Welcome to Leeds</a>
  <a href="#">Rates</a>
  <a href="#">Who's Merle?!</a>
  <a href="#">FAQ's</a>
  <a href="#">Where are we</a>
</nav>

<section class="hero">
  <div class="hero-photo" role="img" aria-label="Photo of a white travel trailer parked on green grass under trees"></div>
  <svg class="arrow" style="left:30px" width="20" height="30" viewBox="0 0 20 30"><path d="M15 4L5 15l10 11" fill="none" stroke="#fff" stroke-width="3"/></svg>
  <svg class="arrow" style="right:30px" width="20" height="30" viewBox="0 0 20 30"><path d="M5 4l10 11L5 26" fill="none" stroke="#fff" stroke-width="3"/></svg>
  <div class="hero-text">
    <h1>MERLE'S RV PARK &amp; LODGE</h1>
    <p>Sed ut perspiciatis unde omnis iste natus error sit voluptatem accusantium doloremque laudantium, totam rem aperiam</p>
    <a class="btn btn-maroon" href="#">Read More</a>
  </div>
  <svg class="hero-curve" width="1200" height="90" viewBox="0 0 1200 90" preserveAspectRatio="none">
    <path d="M0 40 Q600 -20 1200 40 L1200 90 L0 90Z" fill="#3c5624"/>
    <path d="M0 55 Q600 0 1200 55 L1200 90 L0 90Z" fill="#fff"/>
  </svg>
</section>

<section class="welcome">
  <div class="welcome-mark"></div>
  <h2>Welcome to<br>Merle's RV Park &amp; Lodge and Leeds, North Dakota</h2>
  <p>Leeds is in the heart of some of the greatest hunting and fishing in the world. Merle's RV Park is located right on Highway 2 midway between Devils Lake and Rugby North Dakota. We are smack dab in the middle of it all!</p>
</section>

<section class="lodge-intro">
  <h2>MERLE'S LODGE</h2>
  <p class="lead">Are you looking for a cozy, but spacious home away from home? Well, you have found it! Merle's Lodge is 2200 square feet of living space. There are 2 spacious bedrooms with queen sized beds and another common sleeping area with 5 sets of bunk beds. Available to you are 2 restrooms with showers, a great room with dining and relaxing space and a full kitchen. Everything is supplied for you: towels, bedding, cookware, dishware, grill and etc...all that you need to make your stay worry and hassle free. Throw some clothes in a suitcase, hit the road and we will have your home away from home all ready when you get here! The Lodge is open all year round.</p>
  <div class="meeting">
    <h3>Meeting / Conference<br>Space</h3>
    <p>Are you looking for a venue for your next meeting, training event, guys/girls weekend, quilt retreat, holiday gathering, family reunion, birthday, wedding party or get-together? We've got you covered! Merle's Lodge seats about 60 people comfortably. Many of our customers have commented that Merle's was the perfect place for their event because it was so inviting...and just like home!</p>
  </div>
  <div class="meeting-photo" role="img" aria-label="Photo of the lodge great room set with tables and chairs for a meeting"></div>
</section>

<section class="feature-lodge">
  <div class="round-photo" style="left:130px;top:65px;background:radial-gradient(circle at 40% 40%,#8fb36a,#4c6b35)" role="img" aria-label="Photo of a young angler holding a fish by the lake"></div>
  <div class="feature-list" style="position:absolute;left:545px;top:60px">
    <h3>MERLE'S LODGE</h3>
    <ul>
      <li>Groups – hunting, fishing, working, playing</li>
      <li>2200 square feet</li>
      <li>Full Kitchen</li>
      <li>Free WiFi</li>
      <li>Satellite TV</li>
      <li>2 restrooms, one is handicap accessible</li>
      <li>Sleeps 14 – 2 bedrooms with queen sized beds, plus a shared sleeping area with bunk beds</li>
      <li>A great room with ample seating for large groups</li>
      <li>Merle's supplies everything...bedding, towels, cookware, etc.</li>
      <li>Kids stay free.</li>
    </ul>
  </div>
</section>

<section class="rv-park">
  <h2>MERLE'S RV PARK</h2>
  <p>Merle's RV Park sits right next to Highway 2 on the north side. We have 14 full service spaces – sewer, water and electric (20, 30, 50 amp). There is an indoor restroom with shower that is available 24 hours a day to our RV customers. Plenty of space is available to you for parking boats, trailers, etc.</p>
  <p>Merle's RV Park year round, but water usage depends on when spring thaw and freeze up occurs.</p>
  <p style="width:720px">Please note: Merle's RV Park is an unattended RV park. No reservations required. Please pull on in, use our self-service check-in and then sit back and relax!</p>
  <div class="round-photo" style="left:150px;top:425px;background:linear-gradient(180deg,#cfd8e2 0%,#9a3a33 45%,#c9b89a 100%)" role="img" aria-label="Photo of the red-roofed restroom building at the RV park"></div>
  <div class="feature-list" style="position:absolute;left:530px;top:375px;width:600px">
    <h3>MERLE'S RV PARK</h3>
    <div class="sub">14 Full Service Sites</div>
    <ul>
      <li>Electric (20, 30 &amp; 50amp), Water, Sewer</li>
      <li>Free WiFi</li>
      <li>Safe &amp; convenient location</li>
      <li>24 hour indoor restroom with shower</li>
      <li>Road Saver Club accepted for first night</li>
      <li>Ample room to park boats, trailers etc.</li>
      <li>Convenience store/gas station located right across the street. Restaurant onsite.</li>
      <li>Merle's operates on a first come, first serve basis for short term stays. If you would like to reserve for a stay longer than 3 days, please call Merle.</li>
    </ul>
  </div>
</section>

<section class="tents">
  <h2>TENTS</h2>
  <p>Sed ut perspiciatis unde omnis iste natus error sit voluptatem accusantium doloremque laudantium, totam rem aperiam, eaque ipsa quae ab illo inventore veritatis et quasi architecto beatae vitae dicta sunt explicabo. Nemo enim ipsam voluptatem quia voluptas sit aspernatur aut odit aut fugit, sed quia consequuntur magni dolores eos qui ratione voluptatem sequi nesciunt. Neque porro quisquam est, qui dolorem ipsum quia dolor sit amet, consectetur, adipisci velit, sed quia non numquam</p>
  <a class="btn btn-outline-light" href="#">Read More</a>
</section>

<section class="testimonials">
  <h2>Find out what our customers are saying<br>about Merle's RV Park &amp; Lodge.</h2>
  <a class="btn btn-outline" href="#">Click Here</a>
</section>

<footer class="site-footer">
  <div class="footer-brand">
    <span class="brand-mark"></span>
    <span class="brand-name">Merle's RV Park<br>&amp; Lodge<br>Leeds ND</span>
  </div>
  <div class="footer-col" style="left:305px;width:270px">
    <h4>Contact Us</h4>
    <div class="contact-row">
      <svg width="14" height="18" viewBox="0 0 14 18"><path d="M7 1a6 6 0 0 0-6 6c0 4 6 10 6 10s6-6 6-10a6 6 0 0 0-6-6z" fill="#ddd"/><circle cx="7" cy="7" r="2" fill="#161616"/></svg>
      <p>Merle's RV Park &amp; Lodge<br>120 Prairie Lane Leeds ND<br>58346</p>
    </div>
    <div class="contact-row">
      <svg width="14" height="16" viewBox="0 0 14 16"><path d="M2 1h3l1 4-2 1c1 2 3 4 5 5l1-2 4 1v3c-8 1-13-5-12-12z" fill="#ddd"/></svg>
      <p>Phone : 701-555-0188</p>
    </div>
    <div class="contact-row">
      <svg width="16" height="12" viewBox="0 0 16 12"><rect x="0.5" y="0.5" width="15" height="11" fill="none" stroke="#ddd"/><path d="M1 1l7 6 7-6" fill="none" stroke="#ddd"/></svg>
      <p>Email : hello@merlesrvpark.example</p>
    </div>
    <div class="socials"><span></span><span></span><span></span><span></span><span></span></div>
  </div>
  <div class="footer-col" style="left:608px;width:300px">
    <h4>Sign up to receive email</h4>
    <p>Get park news, seasonal rates and lodge openings sent straight to your inbox each month.</p>
    <div class="field">Enter Name</div>
    <span class="btn-subscribe">SUBSCRIBE</span>
  </div>
  <div class="footer-col" style="left:947px;width:160px">
    <h4>Quick Links</h4>
    <ul class="quick-links">
      <li>Home</li>
      <li>Welcome &amp; Information</li>
      <li>Area Attractions</li>
      <li>Welcome to Leeds</li>
      <li>Rates</li>
      <li>Who's Merle?!</li>
      <li>FAQ's</li>
      <li>Where are we</li>
    </ul>
  </div>
  <div class="copyright">Copyright © Merle's RV Park &amp; Lodge 2018. All rights reserved.</div>
</footer>

</body>
</html>
```